Aerospace Center needs app design

We need a design that would be a creative and innovative look of a simple idea connecting air traffic control situations with sonification.
We would like to see designs that use the elements shown in the short video which are different pads, showing 4 different colors, connecting with a degree and feeling of urgency. The different pads will be movable over screen, similar as to a whiteboard where you can move things around. Each of those pads has 4 different elements that are shown:
- ATC Event (you can chose different setups)
- Select a status (you can chose between Information, Caution and Alert. Color needs to feel more alert from Information to Alert.
- Notes box (you can open the box and write additional text on it)
- Music (you can chose different files. on the right side you can see a small group of notes. When you hover over the notes, music will be played without pressing a play or stop button.
The second video is an overview of music archival program that is connected with the pads.
Look and feel
Each slider illustrates characteristics of the customer's brand and the style your logo design should communicate.

```html
<!DOCTYPE html>
<html lang="en">
<head>
<meta charset="utf-8">
<title>SONA – ATC Sound Pads</title>
<link rel="stylesheet" href="https://fonts.googleapis.com/css2?family=Hind:wght@400;500;600;700&display=swap">
<style>
:root{
  --header-top:#5cc3de;
  --header-bottom:#0c8fe0;
  --sidebar:#0d8ee0;
  --sidebar-active:#4fc0dd;
  --white:#ffffff;
  --field-text:#4a4a4a;
  --caret:#2b2b2b;
  --footer-text:#333333;
  --search-bg:#f2f2f2;
  --search-text:#8a8a8a;

  --pad1-top:#0a6fbf; --pad1-bottom:#2ca9ee; --pad1-inner:#5fc4da; --pad1-ring:#c8b65c; --pad1-core:#f2c230; --pad1-scene-a:#4fb9f3; --pad1-scene-b:#1a8edb;
  --pad2-top:#ff5f6f; --pad2-bottom:#ffb51c; --pad2-inner:#fbd406; --pad2-ring:#a9c48c; --pad2-core:#4db8d8; --pad2-scene-a:#f9c417; --pad2-scene-b:#b89406;
  --pad3-top:#2e6e66; --pad3-bottom:#78de28; --pad3-inner:#7be829; --pad3-ring:#27987a; --pad3-core:#0b67b3; --pad3-scene-a:#86e63a; --pad3-scene-b:#3ea812;
  --pad4-top:#870000; --pad4-bottom:#d80000; --pad4-inner:#ff0000; --pad4-ring:#e46a10; --pad4-core:#f7b61e; --pad4-scene-a:#ff5a5a; --pad4-scene-b:#e01616;
}
*{box-sizing:border-box;margin:0;padding:0}
html,body{width:1200px;height:584px;overflow:hidden;background:var(--white);font-family:"Hind",sans-serif}
.app{position:relative;width:1200px;height:584px}

.topbar{position:absolute;left:0;top:0;width:1200px;height:59px;background:linear-gradient(180deg,var(--header-top),var(--header-bottom))}
.brand{position:absolute;left:27px;top:11px;display:flex;align-items:center;gap:9px}
.brand-mark{width:28px;height:28px;border-radius:50%;background:var(--white)}
.brand-name{font-weight:700;font-size:34px;line-height:1;color:var(--white);padding-top:6px;letter-spacing:.5px}
.search{position:absolute;left:619px;top:12px;width:306px;height:31px;border-radius:16px;background:var(--search-bg);display:flex;align-items:center;padding:0 14px;justify-content:space-between}
.search span{font-size:11px;color:var(--search-text);padding-top:2px}
.toggle{position:absolute;left:961px;top:21px;width:35px;height:14px;border-radius:8px;background:var(--white)}
.toggle::after{content:"";position:absolute;right:2px;top:2px;width:10px;height:10px;border-radius:50%;background:var(--header-top)}
.bell{position:absolute;left:1007px;top:21px}
.user{position:absolute;left:1049px;top:11px;display:flex;align-items:center;gap:10px}
.avatar{position:relative;width:36px;height:36px;border-radius:50%;background:linear-gradient(160deg,#c9d2da,#6a7784)}
.avatar .online{position:absolute;right:-1px;top:0;width:8px;height:8px;border-radius:50%;background:#2fe04a}
.user-name{color:var(--white);font-weight:600;font-size:12px;letter-spacing:.3px;padding-top:3px}

.sidebar{position:absolute;left:0;top:76px;width:56px;height:508px;background:var(--sidebar);border-top-right-radius:30px}
.nav-item{position:absolute;left:6px;width:34px;height:34px;display:flex;align-items:center;justify-content:center}
.nav-item.active{border-radius:50%;background:var(--sidebar-active)}
.sidebar .avatar{position:absolute;left:7px;top:389px}

.pad{position:absolute;top:106px;width:245px;height:400px;border-radius:18px;overflow:hidden}
.pad-scene{position:absolute;left:0;right:0;bottom:0;height:148px}
.pad-panel{position:absolute;left:22px;top:17px;width:201px;height:262px;border-radius:12px}
.field{position:absolute;left:15px;width:168px;height:34px;border-radius:17px;background:var(--white);display:flex;align-items:center;justify-content:space-between;padding:2px 16px 0 15px;font-size:11px;color:var(--field-text)}
.field.notes{padding-left:17px}
.caret{width:0;height:0;border-left:4px solid transparent;border-right:4px solid transparent;border-top:4px solid var(--caret);margin-top:-2px}
.f1{top:18px}.f2{top:60px}.f3{top:102px}.f4{top:145px}
.sound{position:absolute;left:74px;top:191px;width:53px;height:53px;border-radius:50%;display:flex;align-items:center;justify-content:center}
.sound-core{width:42px;height:42px;border-radius:50%;display:flex;align-items:center;justify-content:center}

.pad-1{left:108px;background:linear-gradient(180deg,var(--pad1-top),var(--pad1-bottom))}
.pad-1 .pad-scene{background:linear-gradient(180deg,var(--pad1-scene-a),var(--pad1-scene-b))}
.pad-1 .pad-panel{background:var(--pad1-inner)}
.pad-1 .sound{background:var(--pad1-ring)}.pad-1 .sound-core{background:var(--pad1-core)}
.pad-2{left:377px;background:linear-gradient(180deg,var(--pad2-top),var(--pad2-bottom))}
.pad-2 .pad-scene{background:linear-gradient(180deg,var(--pad2-scene-a),var(--pad2-scene-b))}
.pad-2 .pad-panel{background:var(--pad2-inner)}
.pad-2 .sound{background:var(--pad2-ring)}.pad-2 .sound-core{background:var(--pad2-core)}
.pad-3{left:646px;background:linear-gradient(180deg,var(--pad3-top),var(--pad3-bottom))}
.pad-3 .pad-scene{background:linear-gradient(180deg,var(--pad3-scene-a),var(--pad3-scene-b))}
.pad-3 .pad-panel{background:var(--pad3-inner)}
.pad-3 .sound{background:var(--pad3-ring)}.pad-3 .sound-core{background:var(--pad3-core)}
.pad-4{left:915px;background:linear-gradient(180deg,var(--pad4-top),var(--pad4-bottom))}
.pad-4 .pad-scene{background:linear-gradient(180deg,var(--pad4-scene-a),var(--pad4-scene-b))}
.pad-4 .pad-panel{background:var(--pad4-inner)}
.pad-4 .sound{background:var(--pad4-ring)}.pad-4 .sound-core{background:var(--pad4-core)}

.footer{position:absolute;left:0;width:1200px;top:545px;text-align:center;padding-left:18px;font-size:9.5px;color:var(--footer-text)}
.footer .sep{margin:0 10px}
</style>
</head>
<body>
<svg width="0" height="0" style="position:absolute">
  <defs>
    <symbol id="icon-notes" viewBox="0 0 24 24">
      <g fill="none" stroke="currentColor" stroke-width="1.6" stroke-linecap="round">
        <path d="M6 4v11"/><path d="M6 4l4 2"/>
        <path d="M13 9l8-2v9"/><path d="M13 9v10"/><path d="M13 12l8-2"/>
      </g>
      <g fill="none" stroke="currentColor" stroke-width="1.6">
        <ellipse cx="4.4" cy="15.6" rx="2" ry="1.6"/>
        <ellipse cx="11.4" cy="19.6" rx="2" ry="1.6"/>
        <ellipse cx="19.4" cy="16.6" rx="2" ry="1.6"/>
      </g>
    </symbol>
  </defs>
</svg>
<div class="app">
  <header class="topbar">
    <div class="brand"><span class="brand-mark"></span><span class="brand-name">SONA</span></div>
    <div class="search"><span>Search</span>
      <svg width="11" height="11" viewBox="0 0 12 12"><circle cx="5" cy="5" r="3.8" fill="none" stroke="#222" stroke-width="1.6"/><path d="M8 8l3 3" stroke="#222" stroke-width="1.8" stroke-linecap="round"/></svg>
    </div>
    <div class="toggle"></div>
    <svg class="bell" width="11" height="12" viewBox="0 0 12 13"><path d="M6 1c2.4 0 3.6 1.8 3.6 4v3l1.4 2H1l1.4-2V5C2.4 2.8 3.6 1 6 1z" fill="#fff"/><circle cx="6" cy="11.6" r="1.3" fill="#fff"/></svg>
    <div class="user">
      <div class="avatar" role="img" aria-label="User profile photo"><span class="online"></span></div>
      <span class="user-name">ALEX MORA</span>
    </div>
  </header>

  <nav class="sidebar">
    <div class="nav-item active" style="top:20px"><svg width="14" height="12" viewBox="0 0 14 12"><path d="M7 0L0 6h2v6h4V8h2v4h4V6h2z" fill="#fff"/></svg></div>
    <div class="nav-item" style="top:73px"><svg width="12" height="12" viewBox="0 0 12 12"><path d="M2.5 0.5l2 2.5-1.2 1.5c.8 1.6 2.2 3 3.8 3.8L8.6 7l2.5 2-1 2.3C5 11 1 7 .6 1.6z" fill="#fff"/></svg></div>
    <div class="nav-item" style="top:126px"><svg width="14" height="12" viewBox="0 0 14 12"><path d="M7 0L0 6h2v6h4V8h2v4h4V6h2z" fill="#fff"/></svg></div>
    <div class="nav-item" style="top:178px"><svg width="11" height="13" viewBox="0 0 11 13"><circle cx="5.5" cy="3.2" r="3" fill="#fff"/><path d="M0 13c0-4 2.4-6 5.5-6S11 9 11 13z" fill="#fff"/></svg></div>
    <div class="nav-item" style="top:230px"><svg width="16" height="13" viewBox="0 0 16 13"><path d="M1 0v12h15" stroke="#fff" stroke-width="1.4" fill="none"/><rect x="4" y="5" width="2" height="6" fill="#fff"/><rect x="7.5" y="2" width="2" height="9" fill="#fff"/><rect x="11" y="6" width="2" height="5" fill="#fff"/></svg></div>
    <div class="nav-item" style="top:282px"><svg width="16" height="14" viewBox="0 0 16 14"><circle cx="6" cy="8" r="4" fill="none" stroke="#fff" stroke-width="2.6" stroke-dasharray="2 1.3"/><circle cx="6" cy="8" r="1.5" fill="#fff"/><circle cx="12.5" cy="3.5" r="2.4" fill="none" stroke="#fff" stroke-width="1.8" stroke-dasharray="1.4 1"/></svg></div>
    <div class="nav-item" style="top:334px"><svg width="12" height="15" viewBox="0 0 12 15"><path d="M0 0h8l4 4v11H0z" fill="#fff"/><path d="M2.5 7h7M2.5 9.5h7M2.5 12h7" stroke="#0d8ee0" stroke-width="1"/></svg></div>
    <div class="avatar" role="img" aria-label="User profile photo"><span class="online"></span></div>
  </nav>

  <section class="pad pad-1">
    <div class="pad-scene" role="img" aria-label="Airport scene with plane, control tower and terminal in blue tones"></div>
    <div class="pad-panel">
      <div class="field f1">Select atc event<span class="caret"></span></div>
      <div class="field f2">Select status Level<span class="caret"></span></div>
      <div class="field f3 notes">Notes</div>
      <div class="field f4">Select sound file<span class="caret"></span></div>
      <div class="sound"><div class="sound-core" style="color:#1b1b1b"><svg width="24" height="24"><use href="#icon-notes"/></svg></div></div>
    </div>
  </section>

  <section class="pad pad-2">
    <div class="pad-scene" role="img" aria-label="Airport scene with plane, control tower and terminal in yellow tones"></div>
    <div class="pad-panel">
      <div class="field f1">Landing<span class="caret"></span></div>
      <div class="field f2">1.information<span class="caret"></span></div>
      <div class="field f3">Notes</div>
      <div class="field f4">Harbor Toccata<span class="caret"></span></div>
      <div class="sound"><div class="sound-core" style="color:#ffffff"><svg width="24" height="24"><use href="#icon-notes"/></svg></div></div>
    </div>
  </section>

  <section class="pad pad-3">
    <div class="pad-scene" role="img" aria-label="Airport scene with plane, control tower and terminal in green tones"></div>
    <div class="pad-panel">
      <div class="field f1">Departure<span class="caret"></span></div>
      <div class="field f2">2. Caution<span class="caret"></span></div>
      <div class="field f3">Notes</div>
      <div class="field f4">Evening Etude<span class="caret"></span></div>
      <div class="sound"><div class="sound-core" style="color:#ffffff"><svg width="24" height="24"><use href="#icon-notes"/></svg></div></div>
    </div>
  </section>

  <section class="pad pad-4">
    <div class="pad-scene" role="img" aria-label="Airport scene with plane, control tower and terminal in red tones"></div>
    <div class="pad-panel">
      <div class="field f1">Moon<span class="caret"></span></div>
      <div class="field f2">3. Alert<span class="caret"></span></div>
      <div class="field f3">Notes</div>
      <div class="field f4">Hummingbird<span class="caret"></span></div>
      <div class="sound"><div class="sound-core" style="color:#1b1b1b"><svg width="24" height="24"><use href="#icon-notes"/></svg></div></div>
    </div>
  </section>

  <footer class="footer">© Copyright 2021 SONA<span class="sep">|</span>All Rights Reserved</footer>
</div>
</body>
</html>
```